Hurricane Damage Public Adjuster Billboard

I have created several projects with you and have several great designs. I need to format them into a Billboard for upcoming Hurricane Season. Need done in a month. Im also in process of getting an eye catching and easy to remember 800# Vanity phone number like Call 800-Stormsafe or 800- Need Fix? My included past Craft Huddle projects will give you an idea of what colors, schemes, and designs I gravitate towards. 3 past Design projects were 1) 2 Logos where I picked the 1st place and the 2nd place and 2) Index Card where I picked the winner as the Index Card and the 2nd place as a Post Card. Point is, I will pick and pay for 2 winners if they're good. This should help to sweeten the pot. Also, please look at my website for ideas that I like:

www.TheClaimKeeperGroup.com
I want people to feel that I am the best and highest. Level.

I've been getting a lot of quick half effort designs basically cut & pasting my previous projects. Please don't rush and take your time to be creative. A an example, my Biggest Competitor is Vesta Public Adjusting. Their colors are Black and Gold while mine are Blue, White, and Black with a highlight of Orange if possible. I JUST imported a picture of their BillBoard. I need mine better and BLOW AWAY THEIRS. Terms like "Don't be Victimized Twice ?, Don't let the Hurricane Ruin your Life?". "Get Fairly Paid & Move On" "Our Clients Claims are VIP?
Updates

I'm getting a lot of quick half effort ones. I'd rather you take your time and really put some thoughts and effort into it. My Biggest Competitor is Vesta Public Adjusting. They have black & gold colors, while I have Blue, Black, and white.

It needs to blow theirs away. I have imported their Billboard for comparative purposes.

Guy's,
I'll make it easier for you in what I'm looking for. Please look at the Vesta Billboard picture attached.

1) Put my "Blue Shield" to the left, replacing their logo
2) change color patterns from their (Black, Gold, White) to my color schemes of (Black, Blue, White)
3) I want to see my name where their is:

THE
Claim Keeper's Group
EXPERT & LOCAL Public Adjusters
"FOR THE POLICYHOLDER!!"

4) to the right, add the A+Rated logo and QRS+ Accredited logo, 5 Star Zorbix Rated logo, 5 Start PORCHLINE Highly Rated logo, etc..

5) the right side is where you can be creative as I will not have a picture of me there.

"20+ Years of Experience, Recovering Millions for our VIP Clients"

"Your Best, Locally-Based Private Adjuster & Advocate'
"FOR THE POLICYHOLDER!!"

"Don't be victimized Twice!!"

"Don't let the Hurricane Ruin Your Life!!"

This should really help. Also, refer to my website, maybe a couple testimonial fillers?

Thanks all,

marcus@TheClaimKeeperGroup.com

Just imported a few awards that would look great to the right side with all the other 5 Star Ratings and accolades.
This right section could be titled like zmy Website:

5 Star Reviews, Ratings & Awards:
4-5 Logos underneath?

Target Market(s)

Coastal place where a Hurricane 🌀 🌀 Hits

Industry/Entity Type

Hurricane Public Insurance Adjuster

Font styles to use
Sans Serif
Other font styles liked:
• Zurich fonts

Colors
0054AA
0677BA
7BADD7
CADEEF
E8F1F8
EE7325
F08F49
F5BC92
FAE3D3
FDF4ED

Requirements
Must have
• Use my past project logos, colors, and schemes to create eye grabbing BillBoard
Nice to have
Should not have
• Not be too busy, must be Easy to Read, Eye Catchy

```html
<!DOCTYPE html>
<html lang="en">
<head>
<meta charset="utf-8">
<title>Claim Keeper's Group – Hurricane Season Billboard</title>
<link href="https://fonts.googleapis.com/css2?family=Poppins:wght@500;600;700;800&family=Oswald:wght@500;600;700&family=Bebas+Neue&display=swap" rel="stylesheet">
<style>
  :root {
    --ink: #111416;
    --navy: #0a2f7a;
    --brand-blue: #0054aa;
    --mid-blue: #0677ba;
    --bright-blue: #1a8fe6;
    --sky-blue: #7badd7;
    --pale-blue: #cadeef;
    --white: #ffffff;
    --orange: #ee7325;
    --orange-light: #f08f49;
    --rating-red: #e0242b;
    --porch-green: #7cc242;
    --rule: #d3d7db;
  }
  * { box-sizing: border-box; margin: 0; padding: 0; }
  html, body { width: 1199px; height: 1200px; overflow: hidden; background: var(--white); }
  body { position: relative; font-family: "Poppins", sans-serif; }

  .billboard {
    position: absolute; left: 50px; top: 440px;
    width: 1100px; height: 321px; overflow: hidden;
    background: var(--ink);
    box-shadow: 0 6px 18px rgba(0,0,0,.25);
  }
  .storm-backdrop {
    position: absolute; inset: 109px 0 0 0;
    background: linear-gradient(90deg, var(--sky-blue) 0%, #4fb0e6 30%, var(--mid-blue) 62%, var(--brand-blue) 100%);
  }
  .storm-sky {
    position: absolute; left: 0; top: 0; width: 100%; height: 109px;
    background: linear-gradient(90deg, #1d2226 0%, var(--ink) 50%, #1f2a2f 100%);
  }

  .brand-mark {
    position: absolute; left: 40px; top: 80px; width: 300px;
    display: flex; align-items: center; gap: 12px;
  }
  .brand-mark .dot { width: 22px; height: 22px; border-radius: 50%; background: var(--white); flex: none; }
  .brand-mark .name {
    font-family: "Poppins", sans-serif; font-weight: 800; font-size: 30px; line-height: 1.1;
    color: var(--white);
  }

  .tagline {
    position: absolute; left: 358px; top: 32px;
    font-weight: 600; font-size: 17px; color: var(--white); white-space: nowrap;
  }
  .tagline-strong {
    position: absolute; left: 357px; top: 50px;
    font-weight: 800; font-size: 32px; color: var(--bright-blue); white-space: nowrap; letter-spacing: .5px;
  }

  .headline {
    position: absolute; left: 358px; top: 118px;
    font-family: "Bebas Neue", sans-serif; font-size: 48px; line-height: .88; letter-spacing: 1.5px;
  }
  .headline .line-light { color: var(--white); display: block; }
  .headline .line-dark { color: var(--ink); display: block; }

  .promise-box {
    position: absolute; left: 358px; top: 214px; width: 322px; height: 42px;
    background: var(--orange); border-radius: 3px;
    padding: 3px 14px; font-size: 13px; font-weight: 600; line-height: 1.25; color: var(--white);
  }
  .promise-box strong { color: var(--ink); font-weight: 800; }

  .experience {
    position: absolute; left: 692px; top: 206px; width: 168px; height: 52px;
  }
  .experience .years {
    position: absolute; left: 0; top: -4px;
    font-family: "Poppins", sans-serif; font-weight: 800; font-size: 36px; color: var(--bright-blue); line-height: 1;
  }
  .experience .years sup { font-size: 16px; vertical-align: top; position: relative; top: 2px; }
  .experience .claim {
    position: absolute; left: 60px; top: 2px; white-space: nowrap;
    font-family: "Oswald", sans-serif; font-weight: 600; font-size: 11px; line-height: 1.2; color: var(--white);
  }
  .experience .label {
    position: absolute; left: 0; top: 38px; width: 168px; height: 13px;
    background: var(--orange);
    font-family: "Poppins", sans-serif; font-weight: 700; font-size: 8.5px; letter-spacing: 3.2px;
    color: var(--navy); text-align: center; line-height: 13px;
  }
  .award-badge {
    position: absolute; left: 866px; top: 214px; width: 40px; height: 40px; border-radius: 50%;
    background: radial-gradient(circle, #c9ccd2 0%, #7c828c 100%);
  }

  .cta {
    position: absolute; left: 362px; top: 267px; width: 705px; height: 35px;
    border-radius: 18px; background: var(--white); overflow: hidden; display: flex;
  }
  .cta .call {
    width: 332px; background: var(--navy); border-radius: 18px;
    font-family: "Oswald", sans-serif; font-weight: 600; font-size: 22px; color: var(--white);
    display: flex; align-items: center; padding-left: 16px; letter-spacing: .3px; white-space: nowrap;
  }
  .cta .call span { color: var(--bright-blue); margin-left: 8px; }
  .cta .web {
    flex: 1; display: flex; align-items: center; justify-content: center;
    font-family: "Oswald", sans-serif; font-weight: 600; font-size: 22px; color: var(--navy); letter-spacing: .3px;
  }

  .ratings-shield { position: absolute; left: 880px; top: 24px; width: 208px; height: 234px; }
  .ratings-shield svg { position: absolute; inset: 0; }
  .ratings-list {
    position: absolute; left: 28px; top: 30px; width: 152px; text-align: center;
  }
  .rating-item { border-bottom: 1px solid var(--rule); padding: 3px 0 4px; }
  .rating-item:last-child { border-bottom: none; }
  .aplus .title { font-weight: 600; font-size: 15px; color: var(--rating-red); line-height: 1.1; }
  .aplus .desc { font-family: "Times New Roman", serif; font-size: 7px; color: #333; line-height: 1.1; }
  .aplus .src { font-size: 4.5px; color: #555; }
  .zorbix .name { font-weight: 600; font-size: 19px; color: var(--brand-blue); line-height: 1.1; }
  .stars { color: #f4b400; font-size: 9px; letter-spacing: 1px; line-height: 1; }
  .porchline .name { font-weight: 700; font-size: 15px; color: var(--porch-green); line-height: 1.2; }
  .accredit { display: flex; flex-direction: column; align-items: center; gap: 2px; padding-top: 6px; }
  .accredit .badge { width: 66px; height: 24px; border-radius: 3px; background: #1d5f8c; }
  .accredit .note { font-size: 5.5px; font-weight: 700; color: var(--navy); }
</style>
</head>
<body>
  <section class="billboard" aria-label="Claim Keeper's Group hurricane season billboard">
    <div class="storm-sky" role="img" aria-label="Dark storm clouds"></div>
    <div class="storm-backdrop" role="img" aria-label="Hurricane funnel cloud over coastal homes in blue tones"></div>

    <div class="brand-mark">
      <span class="dot"></span>
      <span class="name">Claim Keeper's<br>Group</span>
    </div>

    <p class="tagline">Your Best, Locally-Based Private Adjuster &amp; Advocate</p>
    <p class="tagline-strong">FOR THE POLICYHOLDER!!</p>

    <h1 class="headline">
      <span class="line-light">DON'T LET THE HURRICANE</span>
      <span class="line-dark">RUIN YOUR LIFE!!</span>
    </h1>

    <p class="promise-box">Your Best, Locally-Based Private Adjuster &amp; Advocate <strong>FOR THE POLICYHOLDER!!</strong></p>

    <div class="experience">
      <div class="years">20<sup>+</sup></div>
      <div class="claim">RECOVERING MILLIONS<br>FOR OUR VIP CLIENTS</div>
      <div class="label">YEARS OF EXPERIENCE</div>
    </div>
    <div class="award-badge" aria-hidden="true"></div>

    <div class="cta">
      <div class="call">CALL 850-555-0147<span>GOT CLAIM?</span></div>
      <div class="web">www.theclaimkeepergroup.com</div>
    </div>

    <aside class="ratings-shield" aria-label="Ratings and accreditations">
      <svg viewBox="0 0 208 234" width="208" height="234" aria-hidden="true">
        <path d="M104 3 L118 14 Q160 24 203 26 L200 110 Q196 180 104 231 Q12 180 8 110 L5 26 Q48 24 90 14 Z" fill="#1b2b2c"/>
        <path d="M104 10 L116 19 Q156 29 196 31 L193 110 Q189 175 104 223 Q19 175 15 110 L12 31 Q52 29 92 19 Z" fill="#ffffff"/>
      </svg>
      <div class="ratings-list">
        <div class="rating-item aplus">
          <div class="title">A+ Rating</div>
          <div class="desc">Highest Rating For<br>Public Insurance Adjusters</div>
          <div class="src">(Source: Industry Review)</div>
        </div>
        <div class="rating-item zorbix">
          <div class="name">Zorbix</div>
          <div class="stars">★★★★★</div>
        </div>
        <div class="rating-item porchline">
          <div class="name">porchline</div>
        </div>
        <div class="rating-item accredit">
          <div class="badge"></div>
          <div class="note">QRS Rating: A+</div>
        </div>
      </div>
    </aside>
  </section>
</body>
</html>
```